Bramblewick Forage Business Cards

I need a business card with my logo, number, Facebook account, and some information about what I am selling. Green card with logo on the front. 555-214-8392 phone number, @bramblewickforage Facebook, •Orchardgrass Hay •Alfalfa Hay •Mixed Grass Hay , and “Premium Quality Hay” all written on the back.

Target Market(s)

Hay

Contact Information for Business Card

Phone number, Facebook, different types of hay.

Colors
00AB8E
00BBA5
67D7C9
C6EFE9
E9F9F6

```html
<!DOCTYPE html>
<html lang="en">
<head>
<meta charset="utf-8">
<title>Bramblewick Forage Business Cards</title>
<link href="https://fonts.googleapis.com/css2?family=Arimo:wght@400;700&display=swap" rel="stylesheet">
<style>
  :root {
    --backdrop: #2b2b2b;
    --card: #0c0c0c;
    --green: #1ba54f;
    --white: #ffffff;
    --grey: #bdbdbd;
    --rule: #5a5a5a;
  }
  * { margin: 0; padding: 0; box-sizing: border-box; }
  html, body { width: 1200px; height: 900px; overflow: hidden; }
  body {
    background: var(--backdrop);
    font-family: "Arimo", Arial, sans-serif;
    color: var(--white);
    position: relative;
  }
  .card {
    position: absolute;
    width: 620px;
    height: 354px;
    background: var(--card);
    box-shadow: 0 12px 30px rgba(0,0,0,.55);
  }
  .card--info { left: 60px; top: 490px; }
  .card--brand { left: 520px; top: 60px; }

  .logo-mark {
    width: 96px; height: 96px;
    border-radius: 50%;
    background: var(--green);
    flex: none;
  }

  /* info side */
  .info-head {
    position: absolute; left: 70px; top: 58px;
    display: flex; align-items: center; gap: 26px;
  }
  .info-divider { width: 1px; height: 92px; background: var(--rule); }
  .brand-name { font-weight: 700; font-size: 36px; color: var(--white); }

  .contact-row {
    position: absolute; left: 110px; top: 196px;
    display: flex; align-items: center; gap: 30px;
    font-size: 19px;
  }
  .contact-item { display: flex; align-items: center; gap: 10px; }
  .icon-dot {
    width: 32px; height: 32px; border-radius: 50%;
    background: var(--green);
    display: flex; align-items: center; justify-content: center;
  }
  .contact-rule {
    position: absolute; left: 150px; top: 248px; width: 320px; height: 1px;
    background: linear-gradient(90deg, transparent, var(--rule), transparent);
  }
  .hay-list {
    position: absolute; left: 0; right: 0; top: 264px;
    text-align: center; color: var(--grey); font-size: 18px; line-height: 1.45;
  }
  .hay-list .bullet {
    display: inline-block; width: 10px; height: 10px; border-radius: 50%;
    background: var(--green); margin: 0 8px; vertical-align: middle;
  }

  /* brand side */
  .brand-block {
    position: absolute; left: 120px; top: 120px;
    display: flex; align-items: center; gap: 28px;
  }
  .brand-text .brand-name { font-size: 34px; }
  .brand-phone { font-weight: 700; font-size: 34px; margin-top: 8px; }
</style>
</head>
<body>

  <section class="card card--info" aria-label="Card back">
    <div class="info-head">
      <div class="logo-mark" aria-hidden="true"></div>
      <div class="info-divider"></div>
      <div class="brand-name">Bramblewick Forage</div>
    </div>

    <div class="contact-row">
      <div class="contact-item">
        <span class="icon-dot" aria-hidden="true">
          <svg width="18" height="18" viewBox="0 0 24 24"><path fill="#fff" d="M6.6 10.8a15.1 15.1 0 0 0 6.6 6.6l2.2-2.2c.3-.3.7-.4 1-.2 1.1.4 2.3.6 3.6.6.6 0 1 .4 1 1V20c0 .6-.4 1-1 1A17 17 0 0 1 3 4c0-.6.4-1 1-1h3.5c.6 0 1 .4 1 1 0 1.2.2 2.4.6 3.6.1.3 0 .7-.2 1L6.6 10.8z"/></svg>
        </span>
        <span>555-214-8392</span>
      </div>
      <div class="contact-item">
        <span class="icon-dot" aria-hidden="true"></span>
        <span>@bramblewickforage</span>
      </div>
    </div>

    <div class="contact-rule"></div>

    <div class="hay-list">
      <div>Orchardgrass Hay<span class="bullet"></span>Alfalfa Hay<span class="bullet"></span>Mixed Grass Hay</div>
      <div>Premium Quality Hay</div>
    </div>
  </section>

  <section class="card card--brand" aria-label="Card front">
    <div class="brand-block">
      <div class="logo-mark" aria-hidden="true"></div>
      <div class="brand-text">
        <div class="brand-name">Bramblewick Forage</div>
        <div class="brand-phone">555-214-8392</div>
      </div>
    </div>
  </section>

</body>
</html>
```